Quality Monitoring Company Needs a New Site

We are an established company that has a fair number of clients but the site lacks current design standards that we'd like to keep up with. We'd like to mimic the same style of the site on plinkora.com, vetrumo.com, https://brindlecoffer.com/, etc. We'd also like to make sure the designer understands SEO Silos and how it effects the design elements. Attached is the structure that I'd like to follow for the pages. You don't need to design every single sub-page because they'll probably be fairly similar; however, I want to see at least 1 each. Please use the content on our current site for filler areas. Please try to do a good job of understanding what we do so you can use your best judgement on what is needed to be successful. Use our color scheme and the logo should be the side view but I included the AI just in case.
Updates

I am narrowing down on the field of designs that I have received. There are a lot of similarities between the designs I like and don't like. I'd also like to ensure that some of the inner pages get done in the next 5 days so I can see the creativity that is there as well. That is probably what is next -- getting a few inner pages completed so I can see what you can come up with (not based on our current website) because the current "front pages" are all so good and so close.

Industry/Entity Type

Telecommunications

Colors

Designer to choose colors to be used in the design.

Requirements
Must have
• SEO Silo Look and Feel
• Current Colors
Should not have
• No stockphotos whatsoever. NONE.

```html
<!DOCTYPE html>
<html lang="en">
<head>
<meta charset="utf-8">
<title>Pricing – Vocalyst</title>
<link href="https://fonts.googleapis.com/css2?family=Montserrat:wght@600;700;800&family=Poppins:wght@400;500;600&display=swap" rel="stylesheet">
<style>
:root{
  --navy:#0b2f5c;
  --footer:#062e5a;
  --cyan:#1bb0e6;
  --gray:#8a8f98;
  --text:#4a4f57;
  --bg:#f5f7fb;
  --card:#ffffff;
  --ring-1:#eef6fd;
  --ring-2:#e0eefc;
  --ring-3:#f3f7fc;
}
*{margin:0;padding:0;box-sizing:border-box}
html,body{width:1200px;height:1141px;overflow:hidden;background:var(--bg)}
body{font-family:'Poppins',sans-serif;color:var(--text)}
.page{position:relative;width:1200px;height:1141px;overflow:hidden;background:var(--bg)}
.rings{position:absolute;left:0;top:0}
.brand{position:absolute;left:141px;top:56px;display:flex;align-items:center;gap:8px;color:var(--navy);font-weight:600;font-size:21px}
.brand-dot{width:14px;height:14px;border-radius:50%;background:var(--cyan)}
.nav{position:absolute;top:78px;left:404px;display:flex;gap:0;font-size:12.5px;color:#2d3340}
.nav a{color:inherit;text-decoration:none;position:absolute;white-space:nowrap}
.nav a.active{color:var(--cyan);font-weight:600}
.header-phone{position:absolute;left:903px;top:64px;display:flex;align-items:center;gap:9px}
.header-phone .icon{width:39px;height:39px;border-radius:50%;background:var(--cyan);display:flex;align-items:center;justify-content:center}
.header-phone span{font-family:'Montserrat',sans-serif;font-weight:700;font-size:14px;color:var(--navy)}
.title{position:absolute;left:0;width:1200px;top:192px;text-align:center;font-family:'Montserrat',sans-serif;font-weight:800;font-size:30px;color:var(--navy)}
.title-rule{position:absolute;left:583px;top:243px;width:35px;height:2px;background:var(--cyan)}
.subtitle{position:absolute;left:0;width:1200px;top:259px;text-align:center;font-size:12.5px;color:var(--gray)}
.tiers{position:absolute;left:141px;top:319px;display:flex;gap:15px}
.tier{width:140px;height:126px;background:var(--card);border-radius:9px;text-align:center;padding-top:23px}
.tier .range{font-family:'Montserrat',sans-serif;font-weight:700;font-size:12.2px;color:var(--navy)}
.tier .unit{font-size:12px;color:var(--gray);margin-top:4px;letter-spacing:.3px}
.tier .price{font-family:'Montserrat',sans-serif;font-weight:700;font-size:12.5px;color:var(--cyan);margin-top:6px}
.tier .per{font-size:12px;color:var(--gray);margin-top:7px;letter-spacing:.3px}
.extras{position:absolute;left:141px;top:513px;display:flex;gap:23px}
.extra{width:212px;height:148px;background:var(--card);border-radius:10px;text-align:center;padding-top:18px}
.extra h3{font-family:'Montserrat',sans-serif;font-weight:700;font-size:13px;color:var(--navy)}
.extra .includes{font-family:'Montserrat',sans-serif;font-weight:700;font-size:11px;color:var(--cyan);margin-top:8px}
.extra p{font-size:12px;line-height:20.5px;color:var(--gray);margin-top:3px;padding:0 12px}
.extra .cost{font-family:'Montserrat',sans-serif;font-weight:700;font-size:12.5px;color:var(--navy);margin-top:4px}
.extra .cost.spaced{margin-top:16px}
.cta-text{position:absolute;left:0;width:1200px;top:705px;text-align:center;font-size:11.3px;line-height:19.5px;color:var(--text)}
.cta-button{position:absolute;left:501px;top:767px;width:197px;height:35px;border-radius:18px;background:var(--navy);color:#fff;font-size:13.5px;display:flex;align-items:center;justify-content:center;letter-spacing:.3px}
.footer{position:absolute;left:0;top:873px;width:1200px;height:268px;background:var(--footer);color:#fff}
.footer h4{position:absolute;top:56px;font-family:'Montserrat',sans-serif;font-weight:800;font-size:17px;color:var(--cyan)}
.links{position:absolute;top:97px;font-size:11px;line-height:20.4px}
.contact-line{position:absolute;display:flex;gap:8px;font-size:12.5px;line-height:23px;align-items:flex-start}
.contact-line svg{margin-top:5px;flex:none}
.footer-brand{position:absolute;left:935px;top:70px;display:flex;align-items:center;gap:10px;font-weight:600;font-size:26px;color:#fff}
.footer-brand .dot{width:22px;height:22px;border-radius:50%;background:var(--cyan)}
.footer-rule{position:absolute;left:140px;top:221px;width:919px;height:1px;background:rgba(255,255,255,.15)}
.copyright{position:absolute;left:0;width:1200px;top:237px;text-align:center;font-size:12.5px}
</style>
</head>
<body>
<div class="page">
  <svg class="rings" width="1200" height="560" viewBox="0 0 1200 560" aria-hidden="true">
    <circle cx="967" cy="159" r="332" fill="var(--ring-1)"/>
    <circle cx="967" cy="159" r="233" fill="var(--ring-2)"/>
    <circle cx="967" cy="159" r="162" fill="var(--ring-3)"/>
  </svg>

  <header>
    <div class="brand"><span class="brand-dot"></span>Vocalyst</div>
    <nav class="nav">
      <a style="left:0">Home</a>
      <a style="left:58px">Services</a>
      <a style="left:131px">Industries</a>
      <a class="active" style="left:213px">Pricing</a>
      <a style="left:281px">Team</a>
      <a style="left:338px">Blog</a>
      <a style="left:389px">Contact Us</a>
    </nav>
    <div class="header-phone">
      <div class="icon">
        <svg width="15" height="15" viewBox="0 0 24 24"><path fill="#fff" d="M6.6 10.8a15.1 15.1 0 0 0 6.6 6.6l2.2-2.2c.3-.3.7-.4 1-.2 1.1.4 2.3.6 3.6.6.6 0 1 .4 1 1V20c0 .6-.4 1-1 1C10.6 21 3 13.4 3 4c0-.6.4-1 1-1h3.5c.6 0 1 .4 1 1 0 1.3.2 2.5.6 3.6.1.3 0 .7-.2 1z"/></svg>
      </div>
      <span>800-555-0142</span>
    </div>
  </header>

  <main>
    <h1 class="title">Pricing</h1>
    <div class="title-rule"></div>
    <p class="subtitle">Price per call minute depends on the total number of minutes per month.</p>

    <section class="tiers">
      <div class="tier"><div class="range">30,000 - 100,000</div><div class="unit">Minutes</div><div class="price">$0.20</div><div class="per">Per Minute</div></div>
      <div class="tier"><div class="range">100,000 - 200,000</div><div class="unit">Minutes</div><div class="price">$0.19</div><div class="per">Per Minute</div></div>
      <div class="tier"><div class="range">200,000 - 300,000</div><div class="unit">Minutes</div><div class="price">$0.18</div><div class="per">Per Minute</div></div>
      <div class="tier"><div class="range">300,000 - 400,000</div><div class="unit">Minutes</div><div class="price">$0.17</div><div class="per">Per Minute</div></div>
      <div class="tier"><div class="range">400,000 - 500,000</div><div class="unit">Minutes</div><div class="price">$0.20</div><div class="per">Per Minute</div></div>
      <div class="tier"><div class="range">More Than 500,000</div><div class="unit">Minutes</div><div class="price">$0.20</div><div class="per">Per Minute</div></div>
    </section>

    <section class="extras">
      <div class="extra"><h3>Inital Setup</h3><div class="includes">Includes:</div><p>Scorecard Setup &amp; Client Calibration</p><div class="cost">$999</div></div>
      <div class="extra"><h3>Additional Scorecard</h3><div class="includes">Includes:</div><p>Scorecard Setup and Client Calibration</p><div class="cost">$499</div></div>
      <div class="extra"><h3>Optional</h3><p style="margin-top:8px">Voice-To- Text Transcription + Keyword Spotting + PCI Redaction</p><div class="cost">$.025 / Minute</div></div>
      <div class="extra"><h3>Optional</h3><p style="margin-top:8px">Predictive Model Building Based on Scorecard</p><div class="cost spaced">$5,500 / Month</div></div>
    </section>

    <p class="cta-text">Contact us today to learn more! We will have someone contact you to discuss pricing, show you a demonstration of our<br>system, and answer all of your questions. We look forward to discussing your quality processes!</p>
    <div class="cta-button">CONTACT US NOW</div>
  </main>

  <footer class="footer">
    <h4 style="left:139px">Quick Links</h4>
    <div class="links" style="left:139px">Home<br>Services<br>System Details<br>Pricing</div>
    <div class="links" style="left:294px">Team<br>Blog<br>Contact Us<br>Login</div>

    <h4 style="left:460px">Contact Us</h4>
    <div class="contact-line" style="left:462px;top:96px">
      <svg width="11" height="14" viewBox="0 0 24 30"><path fill="#fff" d="M12 0C5.4 0 0 5.3 0 11.9 0 20.8 12 30 12 30s12-9.2 12-18.1C24 5.3 18.6 0 12 0zm0 16.5a4.6 4.6 0 1 1 0-9.2 4.6 4.6 0 0 1 0 9.2z"/></svg>
      <div>2740 Orchard Blvd.<br>Fairmont, CA 91302</div>
    </div>
    <div class="contact-line" style="left:660px;top:96px">
      <svg width="14" height="14" viewBox="0 0 24 24"><path fill="#fff" d="M6.6 10.8a15.1 15.1 0 0 0 6.6 6.6l2.2-2.2c.3-.3.7-.4 1-.2 1.1.4 2.3.6 3.6.6.6 0 1 .4 1 1V20c0 .6-.4 1-1 1C10.6 21 3 13.4 3 4c0-.6.4-1 1-1h3.5c.6 0 1 .4 1 1 0 1.3.2 2.5.6 3.6.1.3 0 .7-.2 1z"/></svg>
      <div>800-555-0142</div>
    </div>
    <div class="contact-line" style="left:660px;top:131px">
      <svg width="14" height="11" viewBox="0 0 24 18"><path fill="#fff" d="M0 0h24v2L12 10 0 2zM0 4.5l12 8 12-8V18H0z"/></svg>
      <div>hello@vocalyst.com</div>
    </div>

    <div class="footer-brand"><span class="dot"></span>Vocalyst</div>
    <div class="footer-rule"></div>
    <p class="copyright">Copyright © 2019 VOCALYST. All Rights Reserved.</p>
  </footer>
</div>
</body>
</html>
```